Website & Logo The full package New Business new design and idea

Word Press

Simple, clean and very professional and approachable if possible

I am looking for a full business concept from logo to colour pallet and everything in between.
Brand new business concept, the successful applicant may continue on as our outsourced point person for all future work.

I will have an animated explainer video going over the four keys to business success Staff, Product & Services, Marketing, Sales and why the need a coach just like a sporting team to stay focused and clear on measurable outcomes.

Just added script (pdf attachment) i will be using for the explainer video at top of site.
Updates

Target Market(s)

Small business owners in Australia

Industry/Entity Type

Business Consultant

Number of Pages Required

1 page

Font styles to use
Sans Serif

Colors

Designer to choose colors to be used in the design.

Requirements
Must have
• Word press using Divi platform
• Ball park as per pdf uploaded
• Must work on all devices
• Social links
• Clear and straight forward movement through site
• Great capture of name and email,
• Free Download
• 10 Things you can start today in your small business to get you going again!
Nice to have
• clean one page potentially
• Free files and resources page
Should not have
• boring old menu and old framing

```html
<!DOCTYPE html>
<html lang="en">
<head>
<meta charset="utf-8">
<title>Steady Path Coaching</title>
<link href="https://fonts.googleapis.com/css2?family=Lato:wght@400;700;900&display=swap" rel="stylesheet">
<style>
:root{
  --orange:#ef8c12;
  --blue:#13aed6;
  --blue-dark:#0d8fb3;
  --ink:#2b2b2b;
  --text:#4a4a4a;
  --grey:#f1f1f1;
  --navy:#0e1a2b;
  --footer:#3b3b3b;
  --footer-panel:#5a5a5a;
  --white:#ffffff;
}
*{box-sizing:border-box;margin:0;padding:0}
html,body{width:1200px;height:4565px;overflow:hidden}
body{position:relative;background:var(--white);font-family:'Lato',Arial,sans-serif;color:var(--text)}
.abs{position:absolute}
.backdrop{position:absolute;left:0;top:0}
.brand{position:absolute;left:75px;top:46px;font-size:27px;font-weight:700;color:var(--blue);letter-spacing:-.3px}
.nav{position:absolute;top:52px;left:541px;font-size:12px;font-weight:700;color:var(--ink)}
.nav a{text-decoration:none;color:inherit;position:absolute;white-space:nowrap}
.nav .active{color:var(--orange)}
.hero-title{left:73px;top:302px;font-size:52px;line-height:53px;font-weight:900;color:var(--white)}
.hero-sub{left:75px;top:425px;font-size:16px;line-height:27px;color:var(--white)}
.btn{position:absolute;display:flex;align-items:center;justify-content:center;border-radius:22px;font-size:13.5px;font-weight:700;text-transform:uppercase;letter-spacing:.3px;text-decoration:none}
.btn-solid{background:var(--blue);color:var(--white)}
.btn-white{background:var(--white);color:var(--blue)}
.btn-ghost{border:2px solid var(--white);color:var(--white)}
.btn-orange{background:var(--orange);color:var(--white)}
.play-dot{width:18px;height:18px;border-radius:50%;background:var(--blue);margin-right:8px;display:inline-flex;align-items:center;justify-content:center}
.card{left:75px;top:723px;width:1050px;height:302px;background:var(--grey);border-radius:32px}
.h2{position:absolute;font-size:22px;font-weight:700;color:var(--ink);text-transform:uppercase}
.h2.light{color:var(--white)}
.body{position:absolute;font-size:13.5px;line-height:23px;color:var(--text)}
.body.light{color:var(--white)}
.center{text-align:center}
.date{left:75px;top:1107px;font-size:17px;font-weight:700;color:var(--blue)}
.ticks{position:absolute;list-style:none;font-size:13.5px;color:var(--text)}
.ticks li{position:relative;padding-left:33px;line-height:23px;margin-bottom:4.5px}
.ticks li::before{content:"";position:absolute;left:0;top:5px;width:13px;height:13px;border-radius:50%;background:var(--tick,var(--blue))}
.ticks li::after{content:"";position:absolute;left:3px;top:9px;width:4px;height:4px;border-top:2px solid #fff;border-right:2px solid #fff;transform:rotate(45deg)}
.ticks.orange{--tick:var(--orange)}
.art{position:absolute}
.label-orange{left:0;width:1200px;top:2880px;text-align:center;font-size:15px;font-weight:700;color:var(--orange)}
.cta-band{left:0;top:4116px;width:1200px;height:99px;background:linear-gradient(90deg,var(--orange) 0%,#fbe6c4 25%,#fdf4e6 50%,#d7f0f8 75%,var(--blue) 100%)}
.cta-link{left:0;width:1200px;top:4148px;text-align:center;font-size:23px;font-weight:700;color:var(--orange);text-decoration:underline}
.f-head{position:absolute;font-size:17px;font-weight:700;color:var(--white);text-transform:uppercase}
.f-list{position:absolute;list-style:none;font-size:13px;color:#e6e6e6}
.f-list li{line-height:29px}
.input{position:absolute;left:75px;width:330px;height:44px;border-radius:22px;background:var(--white);font-size:14px;color:#444;padding-left:20px;display:flex;align-items:center}
.social{position:absolute;top:4428px;width:24px;height:24px;border-radius:50%;background:var(--white)}
</style>
</head>
<body>

<svg class="backdrop" width="1200" height="4565" viewBox="0 0 1200 4565" aria-hidden="true">
  <rect x="0" y="0" width="1200" height="780" fill="var(--orange)"/>
  <path d="M0 0 H1125 V80 Q1125 105 1100 106 L0 140 Z" fill="var(--white)"/>
  <path d="M75 1450 L1200 1412 V1800 L75 1728 Z" fill="var(--blue)"/>
  <path d="M0 1733 L1095 1770 Q1125 1772 1125 1800 V2082 L0 2118 Z" fill="var(--grey)"/>
  <path d="M75 2092 L1200 2055 V2443 L75 2375 Z" fill="var(--blue)"/>
  <path d="M0 2375 L1095 2412 Q1125 2414 1125 2442 V2735 Q1125 2762 1098 2762 H0 Z" fill="var(--grey)"/>
  <defs>
    <linearGradient id="appBg" x1="0" y1="0" x2="1" y2="1">
      <stop offset="0" stop-color="#16263b"/><stop offset=".5" stop-color="#0b1522"/><stop offset="1" stop-color="#1a2d42"/>
    </linearGradient>
  </defs>
  <rect x="0" y="3190" width="1200" height="328" fill="url(#appBg)"/>
  <rect x="0" y="4215" width="1200" height="350" fill="var(--footer)"/>
  <path d="M0 4240 L400 4262 Q425 4264 432 4288 L520 4565 H0 Z" fill="var(--footer-panel)"/>
</svg>

<div class="brand">STEADY PATH COACHING</div>
<nav class="nav" aria-label="Main">
  <a class="active" style="left:0">HOME</a>
  <a style="left:86px">ABOUT US</a>
  <a style="left:198px">SERVICES</a>
  <a style="left:305px">PRODUCTS</a>
  <a style="left:421px">BLOG</a>
  <a style="left:499px">CONTACT</a>
</nav>

<svg class="art" style="left:478px;top:140px" width="722" height="640" viewBox="0 0 722 640" role="img" aria-label="Illustration of a coach presenting a growth chart to a seated audience in a bright workshop room">
  <defs><linearGradient id="heroArt" x1="0" y1="0" x2="0" y2="1"><stop offset="0" stop-color="#e6ebf5"/><stop offset="1" stop-color="#b9c3da"/></linearGradient></defs>
  <path d="M107 0 H722 V640 H0 Z" fill="url(#heroArt)"/>
</svg>
<h1 class="abs hero-title">STEADY PATH<br>COACHING</h1>
<p class="abs hero-sub">Aenean quis justo vulputate, egestas turpis sed,<br>volutpat arcu incidunt fringilla urna.</p>
<a class="btn btn-white" style="left:75px;top:489px;width:182px;height:40px"><span class="play-dot"><svg width="8" height="9" viewBox="0 0 8 9"><path d="M1 0 L8 4.5 L1 9 Z" fill="#fff"/></svg></span>PLAY VIDEO</a>

<div class="abs card"></div>
<h2 class="h2 center" style="left:75px;width:1050px;top:755px">Welcome to Steady Path Coaching</h2>
<p class="body center" style="left:115px;width:970px;top:805px">Steady Path Coaching is here to help, support and turn your small business around, It may not be easy, it may not be pretty, it may not be conventional or what you want to hear but my only goal is to help you succeed in your small business struggling in Australia.</p>
<p class="body center" style="left:115px;width:970px;top:860px">I offer a 12 week fully supported and personally applied program, each week you complete the activities and we meet over CallDeck where your actions are accountable and measurable.</p>
<a class="btn btn-solid" style="left:510px;top:939px;width:180px;height:41px">Read More</a>

<h2 class="h2" style="left:75px;top:1073px">Australian Small Business Snapshot</h2>
<div class="abs date">NOV 26, 2018</div>
<p class="body" style="left:75px;top:1133px;width:610px">It’s an extremely sad sign of the times when you’re confronted with a myriad of ‘for lease’ signs in shop windows along major shopping hubs.</p>
<p class="body" style="left:75px;top:1188px;width:610px">While most businesses in Australia are small -- accounting for 97 percent of all businesses -- they’re shutting their doors in alarmingly high numbers.</p>
<ul class="ticks" style="left:75px;top:1249px">
  <li>What is the Small Business Failure Rate?</li>
  <li>20% of small businesses fail in their first year</li>
  <li>30% of small business fail in their second year</li>
  <li>50% of small businesses fail after five years in business.</li>
  <li>Finally, 70% of small business owners fail in their 10th year in business.</li>
</ul>
<svg class="art" style="left:727px;top:1055px" width="372" height="372" viewBox="0 0 372 372" role="img" aria-label="Illustration of a cheerful businessman giving a thumbs up beside small business sale tags and rising bars">
  <defs><radialGradient id="snapArt"><stop offset="0" stop-color="#f6e7c6"/><stop offset="1" stop-color="#ffffff"/></radialGradient></defs>
  <rect width="372" height="372" fill="url(#snapArt)"/>
</svg>

<svg class="art" style="left:106px;top:1498px" width="240" height="177" viewBox="0 0 240 177" role="img" aria-label="Illustration of a money bag with a dollar sign and a stopwatch">
  <rect width="240" height="177" rx="20" fill="#2c4aa0" opacity=".35"/>
</svg>
<h2 class="h2 light" style="left:432px;top:1487px">Giving Back Free</h2>
<p class="body light" style="left:432px;top:1536px;width:700px">Steady Path Coaching is offering 4 FREE 12-week coaching one on one support program every 3 months to struggling businesses in 2019 as our way of giving back and helping others in need, just fill out the information sheet and we will let you know as soon as possible.</p>
<a class="btn btn-ghost" style="left:434px;top:1641px;width:180px;height:42px">Read More</a>

<h2 class="h2" style="left:75px;top:1813px">Special Offer - Below Cost Price $200 a Week for 12 Weeks</h2>
<p class="body" style="left:75px;top:1862px;width:680px">Steady Path Coaching is offering this incredible one on one support program to only 12 small business owners in the first quarter in 2019 at below cost, so if you need help now, just fill out the information sheet and we will let you know as soon as possible.</p>
<a class="btn btn-solid" style="left:77px;top:1967px;width:180px;height:42px">Read More</a>
<svg class="art" style="left:851px;top:1799px" width="195" height="231" viewBox="0 0 195 231" role="img" aria-label="Illustration of a gear with a dollar sign and downward arrows">
  <rect width="195" height="231" rx="24" fill="#34496a" opacity=".25"/>
</svg>

<svg class="art" style="left:160px;top:2127px" width="195" height="213" viewBox="0 0 195 213" role="img" aria-label="Illustration of a calendar with a clock">
  <rect width="195" height="213" rx="20" fill="#ffffff" opacity=".55"/>
</svg>
<h2 class="h2 light" style="left:432px;top:2137px">Just a Bit More $400 a Week for 12 Weeks</h2>
<p class="body light" style="left:432px;top:2186px;width:700px">Very limited on application only just 4 clients per quarter, here we provide additional one on one support each week and dive deeper into every element of your business and fast track the changes, just fill out the information sheet and we will let you know as soon as possible.</p>
<a class="btn btn-ghost" style="left:434px;top:2292px;width:180px;height:42px">Read More</a>

<h2 class="h2" style="left:75px;top:2491px">How It All Works</h2>
<p class="body" style="left:75px;top:2541px;width:590px">With your permission I breakdown your business, Staff, Products / Services, Marketing and Sales. Under each of these four key components are up to 30 or more components including your staff training and experience, business financials...</p>
<a class="btn btn-solid" style="left:77px;top:2646px;width:180px;height:43px">Read More</a>
<svg class="art" style="left:709px;top:2437px" width="372" height="275" viewBox="0 0 372 275" role="img" aria-label="Illustration of a team meeting around a table in front of chart boards">
  <rect width="372" height="275" rx="10" fill="#dcdcdc"/>
</svg>

<p class="body center" style="left:60px;width:1080px;top:2808px">Regardless if you’re a Steady Path Coaching Free, Special Offer or Just a Bit More, Small Business Owner you all get one on one direct access to me each week along with &nbsp;mountains of accountable activities to turn your small business around into the dream you had hoped it could be.</p>
<div class="abs label-orange">Activates Include</div>
<ul class="ticks orange" style="left:75px;top:2921px;width:520px">
  <li>Getting a measurable base line of the financials and existing marketing.</li>
  <li>Discussing the past ups and downs and looking forward to the future</li>
  <li>Understanding your product or service and how it fits into the current marketplace.</li>
  <li>Looking into the staff for potential opportunities or training.</li>
</ul>
<ul class="ticks orange" style="left:603px;top:2921px;width:540px">
  <li>Looking to establish a mastermind local group with a successful business</li>
  <li>Partnership opportunities</li>
  <li>Creating and applying marketing objectives</li>
  <li>How to give more to grow</li>
</ul>
<a class="btn btn-solid" style="left:510px;top:3088px;width:180px;height:42px">Read More</a>

<h2 class="h2 light center" style="left:0;width:1176px;top:3258px">Application</h2>
<p class="body light center" style="left:180px;width:816px;top:3309px">Placements are strictly limited to 28 per quarter as they are all managed personally for the best possible outcomes.<br>You must have internet access, put the time aside between 1-2 hours a week on CallDeck and be open to<br>change and motivated and accountable to succeed with every scheduled meeting.</p>
<a class="btn btn-solid" style="left:498px;top:3410px;width:180px;height:41px">Free Download</a>

<svg class="art" style="left:612px;top:3545px" width="588" height="514" viewBox="0 0 588 514" role="img" aria-label="Portrait photograph of the coach in a dark suit, smiling, set against an orange panel">
  <defs><linearGradient id="aboutArt" x1="0" y1="0" x2="0" y2="1"><stop offset="0" stop-color="#2a3550"/><stop offset="1" stop-color="#141a2b"/></linearGradient></defs>
  <path d="M175 60 L588 45 V514 L0 460 Z" fill="var(--orange)"/>
  <rect x="115" y="0" width="336" height="496" rx="40" fill="url(#aboutArt)"/>
</svg>
<h2 class="h2" style="left:75px;top:3667px">About Me</h2>
<p class="body" style="left:75px;top:3718px;width:540px;line-height:27px">I am not superman, I just found myself absorbing information over the past 10 years through some mentors and personal development and see so many small business owners struggling and I got sick of telling myself how I would change things that I eventually &nbsp;approached some businesses for free and asked if they needed a hand and they were over the moon...</p>
<a class="btn btn-solid" style="left:75px;top:3878px;width:180px;height:41px">Read More</a>

<div class="abs cta-band"></div>
<a class="abs cta-link">10 Things you can start today in your small business to get you going again!</a>

<div class="f-head" style="left:75px;top:4294px;font-size:21px">Email Sign Up</div>
<div class="abs" style="left:75px;top:4325px;font-size:11.5px;color:#fff">Vivamus quis diam eget neque pellentesque rhoncus...</div>
<div class="input" style="top:4360px">Enter Name</div>
<div class="input" style="top:4418px">Enter Email Address</div>
<a class="btn btn-orange" style="left:75px;top:4484px;width:150px;height:43px;font-size:16px">Sign Up</a>

<div class="f-head" style="left:526px;top:4270px">Company</div>
<ul class="f-list" style="left:526px;top:4297px">
  <li>Vivamus sed ultricies</li><li>Massa et condimentum</li><li>Nullam a placerat</li><li>Mauris lacus magna</li><li>Porttitor id massa</li><li>Condimentum</li>
</ul>
<div class="f-head" style="left:727px;top:4270px">Resources</div>
<ul class="f-list" style="left:727px;top:4297px">
  <li>Vivamus sed ultricies</li><li>Massa et condimentum</li><li>Nullam a placerat</li><li>Mauris lacus</li>
</ul>
<div class="f-head" style="left:927px;top:4270px">Contact Info</div>
<div class="abs" style="left:927px;top:4298px;font-size:13px;line-height:23px;color:#e6e6e6">42 Harbour Lane,<br>Brightwater, BW 2041</div>
<svg class="abs" style="left:927px;top:4349px" width="14" height="14" viewBox="0 0 24 24" aria-hidden="true"><path d="M6.6 10.8a15 15 0 0 0 6.6 6.6l2.2-2.2c.3-.3.7-.4 1-.2 1.1.4 2.3.6 3.6.6.6 0 1 .4 1 1V20c0 .6-.4 1-1 1A17 17 0 0 1 3 4c0-.6.4-1 1-1h3.5c.6 0 1 .4 1 1 0 1.3.2 2.5.6 3.6.1.3 0 .7-.2 1z" fill="#fff"/></svg>
<div class="abs" style="left:960px;top:4346px;font-size:13px;color:#e6e6e6">1-800-555-0142</div>
<svg class="abs" style="left:927px;top:4377px" width="14" height="12" viewBox="0 0 24 20" aria-hidden="true"><path d="M0 0h24v20H0z" fill="#fff"/><path d="M0 0l12 10L24 0" fill="none" stroke="#3b3b3b" stroke-width="2"/></svg>
<div class="abs" style="left:960px;top:4373px;font-size:13px;color:#e6e6e6">hello@steadypathcoaching.example</div>
<span class="social" style="left:929px" aria-label="Social profile one"></span>
<span class="social" style="left:971px" aria-label="Social profile two"></span>
<span class="social" style="left:1013px" aria-label="Social profile three"></span>
<span class="social" style="left:1055px" aria-label="Social profile four"></span>
<span class="social" style="left:1097px" aria-label="Social profile five"></span>

</body>
</html>
```